Veldmark Supplies Business Card

Professional business card that stand out to our potential customers. Front and back with clean modern design

Industry/Entity Type

Oil and gas

Contact Information for Business Card

Name, address, website , office phone and cell number

Requirements
Must have
• Editable files for each employee

```html
<!DOCTYPE html>
<html lang="en">
<head>
<meta charset="utf-8">
<title>Veldmark Supplies – Business Card</title>
<link rel="stylesheet" href="https://fonts.googleapis.com/css2?family=Montserrat:wght@400;500;800&display=swap">
<style>
  :root {
    --bg: #e4e4e4;
    --paper: #ffffff;
    --brand-red: #e31e25;
    --brand-blue: #0fb0d3;
    --ink: #1d1d1d;
    --card-w: 540px;
    --card-h: 309px;
  }
  * { box-sizing: border-box; margin: 0; padding: 0; }
  html, body {
    width: 1200px; height: 856px; overflow: hidden;
    background: var(--bg);
    font-family: "Montserrat", sans-serif;
  }
  .sheet {
    position: relative; width: 1200px; height: 856px;
    display: flex; align-items: center; justify-content: center; gap: 40px;
  }
  .card {
    position: relative; width: var(--card-w); height: var(--card-h);
    overflow: hidden; box-shadow: 0 6px 18px rgba(0,0,0,.18);
  }
  /* Front */
  .card--front { background: var(--paper); }
  .card__bands, .card__rules { position: absolute; inset: 0; }
  .brand-lockup {
    position: absolute; left: 30px; top: 120px; width: 200px;
    text-align: center; font-weight: 800; font-size: 22px;
    line-height: 1.15; letter-spacing: .5px; text-transform: uppercase;
    color: var(--brand-red);
  }
  .contact {
    position: absolute; left: 292px; top: 38px; color: var(--ink);
  }
  .contact__name {
    font-weight: 800; font-size: 19px; letter-spacing: .5px;
    color: var(--brand-red); text-transform: uppercase;
  }
  .contact__title { font-size: 11px; margin-top: 2px; }
  .contact__address { font-size: 11px; line-height: 1.35; margin-top: 12px; }
  .contact__list { list-style: none; margin-top: 10px; }
  .contact__item {
    display: flex; align-items: center; gap: 8px;
    font-size: 11px; line-height: 1; margin-bottom: 6px;
  }
  .contact__icon {
    width: 14px; height: 14px; background: var(--brand-red);
    display: flex; align-items: center; justify-content: center; flex: none;
  }
  .contact__icon svg { width: 10px; height: 10px; }
  .accent { color: var(--brand-red); }
  /* Back */
  .card--back {
    background: var(--brand-blue);
    display: flex; align-items: center; justify-content: center;
  }
  .brand-lockup--back {
    font-weight: 800; font-size: 34px; letter-spacing: 1px;
    color: var(--paper); text-transform: uppercase; text-align: center; line-height: 1.15;
  }
</style>
</head>
<body>
<main class="sheet">
  <section class="card card--front" aria-label="Business card front">
    <svg class="card__bands" viewBox="0 0 540 309" aria-hidden="true">
      <polygon points="0,295 348,295 340,309 0,309" fill="var(--brand-blue)"/>
      <polygon points="356,280 540,280 540,309 342,309" fill="var(--brand-red)"/>
    </svg>
    <svg class="card__rules" viewBox="0 0 540 309" aria-hidden="true">
      <line x1="252" y1="70" x2="252" y2="250" stroke="var(--brand-blue)" stroke-width="1"/>
      <line x1="260" y1="95" x2="260" y2="215" stroke="var(--brand-red)" stroke-width="1"/>
      <line x1="268" y1="80" x2="268" y2="200" stroke="var(--brand-red)" stroke-width="1"/>
      <line x1="276" y1="60" x2="276" y2="240" stroke="var(--brand-blue)" stroke-width="1"/>
    </svg>
    <div class="brand-lockup">Veldmark<br>Supplies</div>
    <div class="contact">
      <h1 class="contact__name">Dana Whitcombe</h1>
      <p class="contact__title">President</p>
      <p class="contact__address">482 Harlow Ave, Ste<br>210, Midland, TX 79701</p>
      <ul class="contact__list">
        <li class="contact__item">
          <span class="contact__icon"><svg viewBox="0 0 10 10"><path d="M2 1h2l1 2-1 1a5 5 0 0 0 2 2l1-1 2 1v2c0 .6-.4 1-1 1A8 8 0 0 1 1 2c0-.6.4-1 1-1z" fill="#fff"/></svg></span>
          555-014-2837
        </li>
        <li class="contact__item">
          <span class="contact__icon"><svg viewBox="0 0 10 10"><rect x="2.5" y="1" width="5" height="8" rx="1" fill="none" stroke="#fff" stroke-width="1"/><circle cx="5" cy="7.5" r=".5" fill="#fff"/></svg></span>
          555-019-4460
        </li>
        <li class="contact__item">
          <span class="contact__icon"><svg viewBox="0 0 10 10"><rect x="1" y="2.5" width="8" height="5" fill="none" stroke="#fff" stroke-width="1"/><path d="M1 2.5l4 3 4-3" fill="none" stroke="#fff" stroke-width="1"/></svg></span>
          info@veldmarksupplies.com
        </li>
        <li class="contact__item">
          <span class="contact__icon"><svg viewBox="0 0 10 10"><circle cx="5" cy="5" r="3.8" fill="none" stroke="#fff" stroke-width="1"/><ellipse cx="5" cy="5" rx="1.6" ry="3.8" fill="none" stroke="#fff" stroke-width=".8"/><line x1="1.2" y1="5" x2="8.8" y2="5" stroke="#fff" stroke-width=".8"/></svg></span>
          www.<span class="accent">veldmarksupplies</span>.com
        </li>
      </ul>
    </div>
  </section>

  <section class="card card--back" aria-label="Business card back">
    <div class="brand-lockup--back">Veldmark<br>Supplies</div>
  </section>
</main>
</body>
</html>
```